Business Card for Professional Photographer

I'm looking for an eye catching modern clean design that compliments my logo/ website fonts & colours.
I specialise in architecture, corporate & commercial photography so I'm marketing to professional clients rather than portrait / wedding clients.

I would prefer to not have a solid black design.

My logo brand guide is as follows :

Main front font. : Reislust
Main font colour : #fff
Slogan front font : Ubuntu Bold
Monogram front font : Venti Medium
Container colour : #fff

I need print ready files in pdf .png & .eps formats.

Included in the files below are some screen grabs as reference to font & colours etc.

```html
<!DOCTYPE html>
<html lang="en">
<head>
<meta charset="utf-8">
<title>Clear Aperture – Business Card</title>
<link href="https://fonts.googleapis.com/css2?family=Josefin+Sans:wght@300&family=Ubuntu:wght@400;700&display=swap" rel="stylesheet">
<style>
  :root {
    --stage: #e4e4e4;
    --card-white: #f4f4f4;
    --ink: #1c1c1c;
    --black: #0e0e0e;
    --gutter: #e9e9e9;
    --gold: #c9a04a;
    --gold-light: #e8cf86;
    --gold-dark: #a9792f;
    --divider: #c8c8c8;
  }
  * { margin: 0; padding: 0; box-sizing: border-box; }
  html, body { width: 1200px; height: 1015px; overflow: hidden; background: var(--stage); }
  body { position: relative; font-family: "Ubuntu", sans-serif; }

  .card {
    position: absolute;
    left: 290px;
    width: 620px;
    height: 354px;
    box-shadow: 0 10px 28px rgba(0,0,0,.22);
    overflow: hidden;
  }
  .card-back { top: 122px; background: var(--black); }
  .card-front { top: 538px; background: var(--card-white); }

  .gold-edge {
    position: absolute; left: 0; right: 0; bottom: 0; height: 9px;
    background: linear-gradient(90deg, var(--gold-dark), var(--gold-light) 45%, var(--gold) 70%, var(--gold-dark));
  }

  /* Back: photo grid */
  .gallery {
    position: absolute; left: 0; top: 0; right: 0; bottom: 9px;
    display: grid;
    grid-template-columns: 1fr 1fr 1fr;
    grid-template-rows: 1fr 1fr;
    gap: 7px;
    background: var(--gutter);
  }
  .photo { width: 100%; height: 100%; }
  .photo-bride { background: radial-gradient(circle at 50% 65%, #d9d9d9 0%, #8d8d8d 30%, #2a2a2a 70%); }
  .photo-car { background: linear-gradient(160deg, #a98a62 0%, #6c5a48 45%, #2e2a2a 100%); }
  .photo-portrait { background: linear-gradient(170deg, #3a3a30 0%, #5a4a34 50%, #232319 100%); }
  .photo-kitchen { background: linear-gradient(180deg, #f2f2f2 0%, #d6d6d6 70%, #3a3a3a 100%); }
  .photo-bathroom { background: linear-gradient(200deg, #6a6a6a 0%, #d8d8d8 45%, #f5f5f5 100%); }

  .brand-tile {
    background: var(--black);
    display: flex; align-items: center; justify-content: center;
    gap: 9px;
    overflow: hidden;
  }
  .brand-tile .brand-dot {
    flex: none;
    width: 14px; height: 14px; border-radius: 50%;
    border: 2px solid var(--gold);
  }
  .brand-tile .brand-name {
    font-family: "Josefin Sans", sans-serif; font-weight: 300;
    color: var(--gold); font-size: 14px; letter-spacing: 2px;
    white-space: nowrap;
  }

  /* Front */
  .logo-block {
    position: absolute; left: 40px; top: 130px;
    display: flex; align-items: center; gap: 12px;
  }
  .logo-circle {
    flex: none;
    width: 44px; height: 44px; border-radius: 50%;
    border: 3px solid var(--gold);
  }
  .logo-name {
    font-family: "Josefin Sans", sans-serif; font-weight: 300;
    color: var(--gold); font-size: 17px; letter-spacing: 2.5px;
    white-space: nowrap;
  }
  .logo-slogan {
    font-family: "Ubuntu", sans-serif; font-weight: 700;
    color: var(--gold); font-size: 7px; letter-spacing: 1.2px;
    margin-top: 4px; white-space: nowrap;
  }

  .divider {
    position: absolute; left: 330px; top: 42px; width: 1px; height: 200px;
    background: var(--divider);
  }

  .contact { position: absolute; left: 358px; top: 48px; color: var(--ink); }
  .person-name {
    font-weight: 700; color: var(--gold); font-size: 21px; letter-spacing: .3px;
  }
  .person-role { font-size: 15px; margin-bottom: 10px; }
  .contact-line {
    display: flex; align-items: center; gap: 8px;
    font-size: 15px; line-height: 22px;
  }
  .contact-line svg { width: 13px; height: 13px; flex: none; }
  .address { font-size: 15px; line-height: 20px; margin-top: 10px; }
</style>
</head>
<body>

  <section class="card card-back" aria-label="Card back">
    <div class="gallery">
      <div class="photo photo-bride" role="img" aria-label="Fashion photograph of a model in a white gown"></div>
      <div class="photo photo-car" role="img" aria-label="Commercial photograph of a custom hot rod outside a building"></div>
      <div class="photo photo-portrait" role="img" aria-label="Outdoor fashion portrait in dappled light"></div>
      <div class="photo photo-kitchen" role="img" aria-label="Architectural interior photograph of a white kitchen"></div>
      <div class="brand-tile">
        <span class="brand-dot"></span>
        <span class="brand-name">CLEAR APERTURE</span>
      </div>
      <div class="photo photo-bathroom" role="img" aria-label="Architectural interior photograph of a white bathroom"></div>
    </div>
    <div class="gold-edge"></div>
  </section>

  <section class="card card-front" aria-label="Card front">
    <div class="logo-block">
      <span class="logo-circle"></span>
      <div>
        <div class="logo-name">CLEAR APERTURE</div>
        <div class="logo-slogan">Architecture Corporate Commercial</div>
      </div>
    </div>

    <div class="divider"></div>

    <div class="contact">
      <div class="person-name">DANIEL HARPER</div>
      <div class="person-role">Managing Director</div>
      <div class="contact-line">
        <svg viewBox="0 0 16 16" aria-hidden="true"><path fill="#c9a04a" d="M3 1h3l1.5 3.5-2 1.3a9 9 0 0 0 4.7 4.7l1.3-2L15 10v3a2 2 0 0 1-2 2A12 12 0 0 1 1 3a2 2 0 0 1 2-2z"/></svg>
        <span>044-555 010 220</span>
      </div>
      <div class="contact-line">
        <svg viewBox="0 0 16 16" aria-hidden="true"><rect x="1" y="3" width="14" height="10" rx="1" fill="#c9a04a"/><path d="M1.5 3.8 8 9l6.5-5.2" fill="none" stroke="#f4f4f4" stroke-width="1.3"/></svg>
        <span>hello@clearaperture.com</span>
      </div>
      <div class="contact-line">
        <svg viewBox="0 0 16 16" aria-hidden="true"><circle cx="8" cy="8" r="7" fill="#c9a04a"/><path d="M1 8h14M8 1c-3 3-3 11 0 14M8 1c3 3 3 11 0 14" fill="none" stroke="#f4f4f4" stroke-width="1"/></svg>
        <span>www.clearaperture.com</span>
      </div>
      <div class="address">17, Harbour Lane<br>Northvale, 20417</div>
    </div>

    <div class="gold-edge"></div>
  </section>

</body>
</html>
```